Request for Business Card Design

Hi. My name is Marlene, I am looking for a new business card design for my company, Quarrow Signal Instruments, LLC. I really like the design you did for Tarsel Venture and was hoping you could do something similar using our full logo and our mark. I am also open to any raised texture design using our mark. I have attached our full logo, which would need to be somewhere on the card, as well as the mark in both outline and full form, as well as our brand colors / guide. The card does not have to be white, as long as our logo and mark appear. I actually like darker colored business cards more, but am open to all options. If you are interested in working with me, please let me know. We would also take the business card design into letterhead design if you can do that.

```html
<!DOCTYPE html>
<html lang="en">
<head>
<meta charset="utf-8">
<title>Quarrow Signal Instruments — Business Card</title>
<link rel="stylesheet" href="https://fonts.googleapis.com/css2?family=Roboto:wght@400;500;700&display=swap">
<style>
  :root {
    --backdrop: #ababab;
    --card: #1e1e1e;
    --brand-blue: #0f9ec6;
    --text-light: #c9c9c9;
    --text-white: #ffffff;
    --divider: #3c3c3c;
    --back-name: #5a5a5a;
  }
  * { box-sizing: border-box; margin: 0; padding: 0; }
  html, body {
    width: 1093px; height: 1200px; overflow: hidden;
    background: var(--backdrop);
    font-family: "Roboto", Arial, sans-serif;
  }
  .card {
    position: absolute; left: 264px; width: 580px; height: 356px;
    background: var(--card); border-radius: 28px; overflow: hidden;
  }
  .card--front { top: 226px; }
  .card--back { top: 621px; }

  .brand { position: absolute; display: flex; align-items: center; }
  .brand__dot { border-radius: 50%; background: var(--brand-blue); flex: none; }
  .brand__name { font-weight: 700; line-height: 1; color: var(--text-white); }
  .brand__tagline {
    font-weight: 500; font-size: 10px; letter-spacing: 0.4px;
    color: var(--text-white); margin-top: 5px; white-space: nowrap;
  }

  .card--front .brand { left: 30px; top: 152px; gap: 22px; }
  .card--front .brand__dot { width: 52px; height: 52px; }
  .card--front .brand__name { font-size: 33px; letter-spacing: 3px; }

  .divider {
    position: absolute; left: 292px; top: 74px; width: 1px; height: 210px;
    background: var(--divider);
  }
  .contact { position: absolute; left: 312px; top: 88px; color: var(--text-light); }
  .contact__name { font-weight: 700; font-size: 23px; color: var(--brand-blue); line-height: 1.1; }
  .contact__role { font-size: 17px; line-height: 1.1; }
  .contact__list { list-style: none; margin-top: 14px; }
  .contact__item { display: flex; align-items: center; gap: 7px; font-size: 17px; line-height: 21px; }
  .contact__icon { width: 15px; height: 15px; flex: none; fill: none; stroke: var(--brand-blue); stroke-width: 1.6; }
  .contact__address { margin-top: 13px; font-size: 17px; line-height: 21px; }

  .card--back .brand { left: 50%; top: 50%; transform: translate(-50%, -50%); gap: 28px; }
  .card--back .brand__dot { width: 74px; height: 74px; }
  .card--back .brand__name { font-size: 46px; letter-spacing: 5px; color: var(--back-name); }
  .card--back .brand__tagline { font-size: 14px; font-weight: 400; color: var(--back-name); letter-spacing: 0.6px; }
</style>
</head>
<body>
  <section class="card card--front">
    <div class="brand">
      <span class="brand__dot"></span>
      <div>
        <div class="brand__name">QUARROW</div>
        <div class="brand__tagline">SIGNAL INSTRUMENTS</div>
      </div>
    </div>
    <div class="divider"></div>
    <div class="contact">
      <h1 class="contact__name">MARLENE HADLEY</h1>
      <p class="contact__role">Managing Director</p>
      <ul class="contact__list">
        <li class="contact__item">
          <svg class="contact__icon" viewBox="0 0 16 16"><path d="M3 1.5l3 3-1.5 1.8c.8 1.8 2.4 3.4 4.2 4.2L10.5 9l3 3-1.8 2c-5.5-.6-10-5-10.6-10.5z"/></svg>
          052-418 730 264
        </li>
        <li class="contact__item">
          <svg class="contact__icon" viewBox="0 0 16 16"><rect x="1" y="3" width="14" height="10"/><path d="M1 3l7 6 7-6"/></svg>
          hello@quarrowsignal.com
        </li>
        <li class="contact__item">
          <svg class="contact__icon" viewBox="0 0 16 16"><circle cx="8" cy="8" r="6.5"/><ellipse cx="8" cy="8" rx="2.8" ry="6.5"/><path d="M1.5 8h13M2.5 4.8h11M2.5 11.2h11"/></svg>
          www.quarrowsignal.com
        </li>
      </ul>
      <p class="contact__address">87, Fenwick Row, Unit 4<br>30918, Lindenmark</p>
    </div>
  </section>

  <section class="card card--back">
    <div class="brand">
      <span class="brand__dot"></span>
      <div>
        <div class="brand__name">QUARROW</div>
        <div class="brand__tagline">SIGNAL INSTRUMENTS</div>
      </div>
    </div>
  </section>
</body>
</html>
```